Locksmith Business Cards

My father-in-law is in need of new business cards for his locksmith business and I need to impress him. Kindly help me out!

You can see the previous business card attached. It is a family run business in North Wales.

No individual names on the cards.

Key Things to Feature:
- The words "Prompt", "Local", "Reliable" (as you can see under the logo on the website)
- 24h Emergency Service
- Covering All of North Wales, the Wirral and Chester
- The color blue
- A key or a lock would be interesting (similar to the ones that come up when you google locksmith business card)

Optional (only if design includes bullet points, like the example below):
https://imgvaultcdn.net/samples/208314/55172/55172_3904821_208314_image.jpg
- Residential / Commercial / Automotive
- Alarms & Cameras
- Key Cutting & Safes

https://www.brynhafod-locksmiths.co.uk/

Industry/Entity Type

Locksmith

Contact Information for Business Card

01632 960 418
07700 900 362
brynhafodlocksmiths@mailvane.com
Brynhafod Locksmiths, The Willow Barn, 7 Tannery Rd., Llandudno LL99 4QX
www.brynhafod-locksmiths.co.uk

Requirements
Must have
• - The words "Prompt", "Local", "Reliable" (as you can see under the logo on the website)
• - 24h Emergency Service
• - Covering All of North Wales, the Wirral and Chester
Nice to have
• - A key or a lock would be interesting (similar to the ones that come up when you google locksmith business card)

```html
<!DOCTYPE html>
<html lang="en">
<head>
<meta charset="utf-8">
<title>Brynhafod Locksmiths – Business Card</title>
<link rel="stylesheet" href="https://fonts.googleapis.com/css2?family=Oswald:wght@400;500&family=Montserrat:wght@500&display=swap">
<style>
  :root {
    --page-bg: #d8dbe1;
    --card-bg: #eef0f4;
    --navy: #1f2a66;
    --mid-blue: #3e5096;
    --band-blue: #3b4f9a;
    --tag-text: #e6e9f2;
  }
  html, body {
    margin: 0;
    width: 1200px;
    height: 1054px;
    overflow: hidden;
    background: var(--page-bg);
  }
  .card {
    position: absolute;
    left: 100px;
    top: 224px;
    width: 1000px;
    height: 605px;
    background: var(--card-bg);
    border-radius: 4px;
    box-shadow: 0 10px 30px rgba(20, 30, 60, 0.18);
    overflow: hidden;
    font-family: "Oswald", sans-serif;
    color: var(--navy);
  }
  .brand-mark {
    position: absolute;
    left: 56px;
    top: 104px;
    width: 108px;
    height: 108px;
    background: var(--navy);
    border-radius: 16px;
  }
  .brand-name {
    position: absolute;
    left: 197px;
    top: 68px;
    margin: 0;
    font-family: "Oswald", sans-serif;
    font-weight: 400;
    font-size: 80px;
    line-height: 84px;
    letter-spacing: 0.5px;
    text-transform: uppercase;
    color: var(--navy);
  }
  .service {
    position: absolute;
    left: 54px;
    top: 334px;
  }
  .service-title {
    margin: 0;
    font-size: 37px;
    font-weight: 400;
    color: var(--mid-blue);
    line-height: 1.2;
  }
  .service-area {
    margin: 4px 0 0;
    font-size: 22px;
    font-weight: 400;
    line-height: 30px;
    color: var(--navy);
  }
  .address {
    position: absolute;
    left: 54px;
    top: 472px;
    margin: 0;
    font-style: normal;
    font-size: 25px;
    line-height: 40px;
    color: var(--navy);
  }
  .contact-list {
    position: absolute;
    left: 536px;
    top: 336px;
    margin: 0;
    padding: 0;
    list-style: none;
  }
  .contact-item {
    display: flex;
    align-items: center;
    height: 40px;
    font-size: 25px;
    color: var(--navy);
  }
  .contact-icon {
    width: 22px;
    height: 22px;
    margin-right: 22px;
    fill: var(--navy);
  }
  .card-bands {
    position: absolute;
    left: 0;
    top: 0;
  }
  .tagline {
    position: absolute;
    left: 530px;
    top: 552px;
    width: 420px;
    margin: 0;
    font-family: "Montserrat", sans-serif;
    font-weight: 500;
    font-size: 21px;
    letter-spacing: 2px;
    color: var(--tag-text);
    white-space: nowrap;
  }
  .tagline .divider { margin: 0 12px; }
</style>
</head>
<body>
  <div class="card">
    <svg class="card-bands" width="1000" height="605" viewBox="0 0 1000 605" aria-hidden="true">
      <rect x="0" y="581" width="1000" height="24" fill="var(--band-blue)"/>
      <polygon points="492,530 1000,530 1000,605 440,605" fill="var(--navy)"/>
    </svg>

    <div class="brand-mark" aria-hidden="true"></div>
    <h1 class="brand-name">Brynhafod<br>Locksmiths</h1>

    <div class="service">
      <p class="service-title">24h Emergency Service</p>
      <p class="service-area">Covering All of North Wales,<br>the Wirral and Chester</p>
    </div>

    <address class="address">The Willow Barn, 7 Tannery Rd.,<br>Llandudno LL99 4QX</address>

    <ul class="contact-list">
      <li class="contact-item">
        <svg class="contact-icon" viewBox="0 0 24 24" aria-hidden="true"><path d="M2 8c0-3 4-4 10-4s10 1 10 4v2h-5V8H7v2H2z M6 12h12l3 8H3z M12 14a2.5 2.5 0 1 0 0 5a2.5 2.5 0 0 0 0-5z"/></svg>
        01632 960 418
      </li>
      <li class="contact-item">
        <svg class="contact-icon" viewBox="0 0 24 24" aria-hidden="true"><path d="M2 8c0-3 4-4 10-4s10 1 10 4v2h-5V8H7v2H2z M6 12h12l3 8H3z M12 14a2.5 2.5 0 1 0 0 5a2.5 2.5 0 0 0 0-5z"/></svg>
        07700 900 362
      </li>
      <li class="contact-item">
        <svg class="contact-icon" viewBox="0 0 24 24" aria-hidden="true"><path d="M2 5h20v14H2z M4 7v1l8 5 8-5V7l-8 5z" fill-rule="evenodd"/></svg>
        brynhafodlocksmiths@mailvane.com
      </li>
      <li class="contact-item">
        <svg class="contact-icon" viewBox="0 0 24 24" aria-hidden="true"><path d="M12 2a10 10 0 1 0 0 20a10 10 0 0 0 0-20zm0 2c1.3 1.5 2.2 3.6 2.4 7H9.6c.2-3.4 1.1-5.5 2.4-7zM7.6 11H4.1A8 8 0 0 1 9 4.6C8.2 6.3 7.7 8.5 7.6 11zm8.8 0c-.1-2.5-.6-4.700-1.4-6.4A8 8 0 0 1 19.9 11zM4.1 13h3.5c.1 2.5.6 4.7 1.4 6.4A8 8 0 0 1 4.1 13zm5.5 0h4.8c-.2 3.4-1.1 5.5-2.4 7-1.3-1.5-2.2-3.6-2.4-7zm6.8 0h3.5a8 8 0 0 1-4.9 6.4c.8-1.7 1.3-3.9 1.4-6.4z"/></svg>
        www.brynhafod-locksmiths.co.uk
      </li>
    </ul>

    <p class="tagline">PROMPT<span class="divider">|</span>LOCAL<span class="divider">|</span>RELIABLE</p>
  </div>
</body>
</html>
```